Willow Cradle Pregnancy and Baby Massage

I need a web design for a new business, WILLOW CRADLE PREGNANCY AND BABY MASSAGE that I am in the process of setting up in the suburbs of Perth, Western Australia. The business is owned and operated by myself and my intention is to service Pregnant Mothers and Parents of Young Babies that would benefit from massage. I would like to have a "Home Page" and pages for "About Me", "Pregnancy Massage", "Baby Massage", a Pricing Page for Pregnancy Massage Sessions, a Pricing Page for Baby Massage Sessions, and a "Contact Me" page to allow clients to either contact me with queries or book available pregnancy massage sessions on a particular day of the week. I would also like a "News" page that would include articles I have written, news about new courses and a link to my Facebook page (yet to be set up). I would like to keep the colour schemes similar to my logo design colours. I need the design to be easy to follow and to appeal to a younger audience (20's to mid 30's).
The target audience is pregnant mothers-to-be wishing to receive massage treatments, and new parents and grandparents of small babies that would like to learn how to massage their babies.
The look and feel should be modern, professional, elegant and feminine.
I need the design to be in a standard format such that I can update the content by myself ( and does not need specialised software) as the company and business progresses.

Target Market(s)

Contact Information for Business Card

Card should have rounded edges. Design should have the same "feel" as the website. Contact Details of my business address, mobile phone, email and website should be included.

Font styles to use
Script

Requirements
Must have
• Same colours as logo design. In cmyk system, the colours are: 20,60,0,0 which best result is pantone 681 and 40,40,0,0 which best result is pantone 2645. Card should include the logo design.

```html
<!DOCTYPE html>
<html lang="en">
<head>
<meta charset="utf-8">
<title>About – Willow Cradle Pregnancy and Baby Massage</title>
<link rel="stylesheet" href="https://fonts.googleapis.com/css2?family=Arimo:wght@400;700&display=swap">
<style>
  :root {
    --band: #9fc3bf;
    --page: #ebe3e3;
    --accent: #d4609f;
    --portrait: #9a7dbf;
    --crumb: #c9cdcc;
    --ink: #2f4a3c;
  }
  * { box-sizing: border-box; margin: 0; padding: 0; }
  html, body { width: 734px; height: 1200px; overflow: hidden; }
  body {
    position: relative;
    background: var(--page);
    font-family: "Arimo", Arial, sans-serif;
    color: var(--ink);
  }
  .site-header {
    position: absolute; top: 0; left: 0; width: 734px; height: 84px;
    background: var(--band);
  }
  .menu-toggle { position: absolute; left: 14px; top: 22px; }
  .search-toggle { position: absolute; right: 14px; top: 18px; }
  .brand {
    position: absolute; left: 50%; top: 18px; transform: translateX(-50%);
    display: flex; align-items: center; gap: 8px;
    color: var(--accent); font-size: 17px; font-weight: 400; text-align: center;
    line-height: 1.1;
  }
  .brand-dot { width: 14px; height: 14px; border-radius: 50%; background: var(--accent); flex: none; }
  .brand-name small { display: block; font-size: 11px; }
  .breadcrumb {
    position: absolute; left: 52px; top: 114px; width: 115px; height: 26px;
    background: var(--crumb); color: var(--accent);
    font-size: 13px; line-height: 26px; text-align: center;
  }
  .portrait {
    position: absolute; left: 160px; top: 202px; width: 412px; height: 412px;
    border-radius: 50%; background: var(--portrait);
  }
  .about-text {
    position: absolute; left: 44px; top: 616px; width: 640px;
    font-size: 21px; line-height: 22.8px;
  }
  .site-footer {
    position: absolute; left: 0; top: 1118px; width: 734px; height: 82px;
    background: var(--band);
    display: flex; justify-content: space-around; align-items: center;
    padding: 0 40px;
  }
  .social-link { width: 36px; height: 36px; border-radius: 50%; background: var(--accent); display: block; }
</style>
</head>
<body>
  <header class="site-header">
    <svg class="menu-toggle" width="52" height="40" viewBox="0 0 52 40" aria-label="Menu">
      <rect x="0" y="0" width="52" height="8" rx="4" fill="var(--accent)"/>
      <rect x="0" y="16" width="52" height="8" rx="4" fill="var(--accent)"/>
      <rect x="0" y="32" width="52" height="8" rx="4" fill="var(--accent)"/>
    </svg>
    <div class="brand">
      <span class="brand-dot"></span>
      <span class="brand-name">Willow Cradle<small>Pregnancy and Baby Massage</small></span>
    </div>
    <svg class="search-toggle" width="50" height="50" viewBox="0 0 50 50" aria-label="Search">
      <circle cx="20" cy="20" r="14" fill="none" stroke="var(--accent)" stroke-width="6"/>
      <line x1="30" y1="30" x2="46" y2="46" stroke="var(--accent)" stroke-width="8" stroke-linecap="round"/>
    </svg>
  </header>

  <nav class="breadcrumb">Home &lt; About</nav>

  <div class="portrait" role="img" aria-label="Portrait illustration of Maren, the practitioner"></div>

  <main class="about-text">
    <p>Maren is a Practitioner of Pregnancy Massage, and a Paediatric Massage Consultant. She completed her training with Bloomwell Prenatal Academy, and the Little Touch Infant Massage Institute. The LTIMI is endorsed by the Southern College of Midwifery. The Coastal Natural Therapies Society, and accredited by the Guild of Massage Practitioners.</p>
    <p>Maren is also a Registered Nurse and Midwife. Most of her professional career has been as a midwife, which has included working in the community in the UK, providing ante natal care and classes, intra partum care, home births, and postnatal care in the home. Maren has also worked in the private and public maternity sectors in Perth.</p>
    <p>Maren was introduced to the wonderful benefits of pregnancy and baby massage after a career change. Working as a Practitioner of Pregnancy Massage, and Paediatric Massage Consultant, enables her to continue working with mothers and babies.</p>
  </main>

  <footer class="site-footer">
    <a class="social-link" aria-label="Social page one"></a>
    <a class="social-link" aria-label="Social page two"></a>
    <a class="social-link" aria-label="Social page three"></a>
    <a class="social-link" aria-label="Social page four"></a>
  </footer>
</body>
</html>
```